Construction Company

Design a clutter free business card, it can be double-sided utilizing the logo for VKM Ltd simple with all relevant contact information.

Please also a letterhead design to function for the purposes of invoicing, all mail requirements, with header to be distinctive while the footer ties page together and incorporates all necessary information.

For now, please use generic / dummy text and when a winner is selected, I will disclose the contact information.

Hi Designers! Please read the updated brief which includes the design of a business card and letterhead. Thank you!

```html
<!DOCTYPE html>
<html lang="en">
<head>
<meta charset="utf-8">
<title>VKM Ltd — Business Card</title>
<link href="https://fonts.googleapis.com/css2?family=Work+Sans:wght@400;600;700&display=swap" rel="stylesheet">
<style>
  :root {
    --royal-blue: #0a2f96;
    --pattern-blue: #1340a8;
    --gold: #b8921a;
    --ink: #3a3a3a;
    --paper: #ffffff;
    --backdrop: #e6e7ea;
  }
  * { box-sizing: border-box; margin: 0; padding: 0; }
  html, body {
    width: 1200px; height: 881px; overflow: hidden;
    background: var(--backdrop);
    font-family: "Work Sans", Arial, sans-serif;
  }
  .sheet {
    width: 1200px; height: 881px;
    display: flex; flex-direction: column;
    align-items: center; justify-content: center; gap: 56px;
  }
  .card {
    position: relative;
    width: 630px; height: 360px;
    border-radius: 16px;
    overflow: hidden;
    box-shadow: 0 6px 18px rgba(0,0,0,.18);
  }
  /* Back side */
  .card-back { background: var(--royal-blue); }
  .card-back .pattern-field {
    position: absolute; inset: 0;
    background: radial-gradient(ellipse at center, var(--pattern-blue) 0%, var(--royal-blue) 75%);
  }
  .card-back .brand-name {
    position: absolute; left: 0; right: 0; top: 50%;
    transform: translateY(-50%);
    text-align: center;
    font-weight: 700; font-size: 64px; letter-spacing: 2px;
    color: var(--paper);
  }
  /* Front side */
  .card-front { background: var(--paper); }
  .card-front .brand-name {
    position: absolute; left: 46px; top: 38px;
    font-weight: 700; font-size: 44px; letter-spacing: 1px;
    color: var(--royal-blue);
  }
  .card-front .accent-bar {
    position: absolute; left: 0; top: 178px;
    width: 10px; height: 46px;
    background: var(--gold);
  }
  .card-front .details {
    position: absolute; left: 50px; top: 150px;
    color: var(--ink);
  }
  .person-name {
    font-weight: 700; font-size: 26px; letter-spacing: 2.5px;
    color: var(--royal-blue); text-transform: uppercase;
  }
  .person-role { font-size: 18px; letter-spacing: 1px; margin-top: 2px; }
  .address { font-size: 17px; letter-spacing: 1.2px; line-height: 1.3; margin-top: 14px; }
  .contact-list { list-style: none; margin-top: 12px; }
  .contact-list li {
    display: flex; align-items: center; gap: 10px;
    font-size: 17px; letter-spacing: 1.2px; line-height: 1.45;
  }
  .contact-list svg { width: 15px; height: 15px; flex: none; }
</style>
</head>
<body>
<main class="sheet">
  <section class="card card-back" aria-label="Card back">
    <div class="pattern-field" role="img" aria-label="Repeated floral brand pattern in soft blue"></div>
    <div class="brand-name">VKM Ltd</div>
  </section>

  <section class="card card-front" aria-label="Card front">
    <div class="brand-name">VKM Ltd</div>
    <div class="accent-bar"></div>
    <div class="details">
      <p class="person-name">Daniel Hartley</p>
      <p class="person-role">Founder</p>
      <p class="address">815 Linden Avenue<br>Riverton, DE 19120</p>
      <ul class="contact-list">
        <li>
          <svg viewBox="0 0 16 16" aria-hidden="true"><path d="M4 1.5l2.3 3-1.4 1.6c.8 1.8 2.2 3.2 4 4l1.6-1.4 3 2.3-1.2 2.5C7 13.5 2.5 9 2 3z" fill="var(--royal-blue)"/></svg>
          (555) 204-7781
        </li>
        <li>
          <svg viewBox="0 0 16 16" aria-hidden="true"><rect x="1.5" y="3.5" width="13" height="9" rx="1" fill="none" stroke="var(--royal-blue)" stroke-width="1.5"/><path d="M2 4l6 5 6-5" fill="none" stroke="var(--royal-blue)" stroke-width="1.5"/></svg>
          info@vkmltd.com
        </li>
        <li>
          <svg viewBox="0 0 16 16" aria-hidden="true"><g fill="none" stroke="var(--royal-blue)" stroke-width="1.3"><circle cx="8" cy="8" r="6.3"/><ellipse cx="8" cy="8" rx="2.8" ry="6.3"/><path d="M1.7 8h12.6M2.8 4.8h10.4M2.8 11.2h10.4"/></g></svg>
          www.vkmltd.com
        </li>
      </ul>
    </div>
  </section>
</main>
</body>
</html>
```